Full re-design of visual identity

We have just re-designed our logo and would like to apply it on our folders, business cards, stationery, and etc... we are attaching new logo + the material we need to re-design... we will provide full corel draw files to help make job easier and also because lot of icons and artwork can be still used...

any doubts we are at your disposal. thanks in advance.

```html
<!DOCTYPE html>
<html lang="en">
<head>
<meta charset="utf-8">
<title>Corvale Business Card</title>
<link rel="stylesheet" href="https://fonts.googleapis.com/css2?family=Open+Sans:wght@300;400;600&display=swap">
<style>
  :root {
    --page-bg: #efefef;
    --card-dark: #4d4d4f;
    --card-light: #ffffff;
    --brand-grey: #8f8f91;
    --ink: #3a3a3c;
    --ink-soft: #6b6b6d;
    --accent: #ee7a33;
    --rule: #4d4d4f;
  }
  * { margin: 0; padding: 0; box-sizing: border-box; }
  html, body { width: 1200px; height: 1000px; overflow: hidden; }
  body {
    background: var(--page-bg);
    font-family: "Open Sans", Arial, sans-serif;
    position: relative;
  }
  .card {
    position: absolute;
    top: 352px;
    width: 520px;
    height: 297px;
    box-shadow: 0 2px 10px rgba(0,0,0,0.08);
    overflow: hidden;
  }
  /* Front */
  .card--front { left: 50px; background: var(--card-dark); }
  .front-brand {
    position: absolute;
    left: 0; right: 0; top: 108px;
    text-align: center;
  }
  .front-brand__name {
    display: inline-flex;
    align-items: center;
    gap: 12px;
    font-size: 54px;
    font-weight: 600;
    color: var(--brand-grey);
    letter-spacing: -1px;
    line-height: 1;
  }
  .brand-mark {
    width: 26px; height: 26px;
    border-radius: 50%;
    background: var(--accent);
  }
  .front-brand__tagline {
    margin-top: 10px;
    font-size: 15px;
    font-weight: 400;
    color: var(--brand-grey);
    letter-spacing: 0.5px;
  }
  /* Back */
  .card--back { left: 630px; background: var(--card-light); }
  .back-accent-band {
    position: absolute;
    left: 0; right: 0; bottom: 0;
    height: 9px;
    background: var(--accent);
  }
  .back-edge-tab {
    position: absolute;
    left: 0; top: 150px;
    width: 5px; height: 64px;
    background: var(--rule);
  }
  .person {
    position: absolute;
    left: 50px; top: 108px;
  }
  .person__name {
    font-size: 30px;
    font-weight: 300;
    color: var(--ink);
    line-height: 1.1;
  }
  .person__title {
    margin-top: 4px;
    font-size: 14px;
    font-weight: 400;
    color: var(--accent);
  }
  .back-divider {
    position: absolute;
    left: 276px; top: 92px;
    width: 1px; height: 92px;
    background: var(--ink-soft);
  }
  .back-brand {
    position: absolute;
    right: 30px; top: 26px;
    display: flex; align-items: center; gap: 6px;
    font-size: 22px;
    font-weight: 600;
    color: var(--brand-grey);
    line-height: 1;
  }
  .back-brand .brand-mark { width: 11px; height: 11px; }
  .contact-list {
    position: absolute;
    left: 300px; top: 82px;
    list-style: none;
    font-size: 11px;
    color: var(--ink-soft);
    line-height: 1.35;
  }
  .contact-list li {
    display: flex; align-items: flex-start; gap: 8px;
    margin-bottom: 4px;
  }
  .contact-list svg { width: 10px; height: 10px; flex: none; margin-top: 2px; fill: var(--accent); }
</style>
</head>
<body>
  <section class="card card--front" aria-label="Business card front">
    <div class="front-brand">
      <div class="front-brand__name">corvale<span class="brand-mark"></span></div>
      <p class="front-brand__tagline">telecom · tecnologia · internet</p>
    </div>
  </section>

  <section class="card card--back" aria-label="Business card back">
    <div class="back-brand">corvale<span class="brand-mark"></span></div>
    <div class="back-edge-tab"></div>
    <div class="person">
      <h1 class="person__name">Daniel Reyes</h1>
      <p class="person__title">Chief Executive Officer</p>
    </div>
    <div class="back-divider"></div>
    <ul class="contact-list">
      <li>
        <svg viewBox="0 0 10 10"><path d="M5 0a3.5 3.5 0 0 0-3.5 3.5C1.5 6 5 10 5 10s3.5-4 3.5-6.5A3.5 3.5 0 0 0 5 0zm0 5a1.4 1.4 0 1 1 0-2.8A1.4 1.4 0 0 1 5 5z"/></svg>
        <span>12 Main Street, Anytown,<br>Postal Code, Country</span>
      </li>
      <li>
        <svg viewBox="0 0 10 10"><path d="M2 0l2 2.5-1.2 1.2a6 6 0 0 0 3.5 3.5L7.5 6 10 8l-1.5 2C4 10 0 6 0 1.5z"/></svg>
        <span>555-123-456</span>
      </li>
      <li>
        <svg viewBox="0 0 10 10"><rect x="0" y="1.5" width="10" height="7" rx="1"/></svg>
        <span>mail@domain.com</span>
      </li>
      <li>
        <svg viewBox="0 0 10 10"><circle cx="5" cy="5" r="5"/></svg>
        <span>www.domain.com</span>
      </li>
    </ul>
    <div class="back-accent-band"></div>
  </section>
</body>
</html>
```